develop our online residential property development appraisal service

This project requires a detailed WordPress design to represent a new digital residential property development consultancy business. At its heart it will have a number of different products that essentially advise customers of the potential value and feasibility of developing their residential site into multiple townhouses, units, apartments, etc... This will be accompanied by explaining the considerations of residential property development.

We aim to navigate and break down this complex area and provide our customers with the tools, knowledge, control and power to 'unlock the value' in their property.

REFERENCE DOCUMENTS:
1. Detailed solution requirements please refer to the attached 'wordpressdesignrequirements'
2. Logo files, style guide and colour pallet please refer to the attached 'KRLM.zip'
3. Site Map refer to attached 'wordpressdesignsitemap'

Reason: Additional information provided so extending period for designs to take into account.

Target Market(s)

The site will appeal to professional service providers; accountants, financial planners, lawyers, etc…

Industry/Entity Type

Residential

Font styles to use
Sans Serif
Other font styles liked:
• Similar to the logo font, slim line and simple

Requirements
Must have
• The logo, style and colour palette provided in the attached 'KRLM.zip' files
• Satisfy the intent of the 'wordpressdesignrequirements'
• Present as an online-centric business
• Clean, crisp and modern design
• Predominant use of white as a background contrasted with the colours provided in the colour palette
Nice to have
• Use of the following WordPress business themes is encouraged but not mandatory:
• 1. Mavo
• 2. Tulek
• 3. Vupa
Should not have
• Overt references to Australia

```html
<!DOCTYPE html>
<html lang="en">
<head>
<meta charset="utf-8">
<title>KRLM — Property Development Appraisals</title>
<link rel="stylesheet" href="https://fonts.googleapis.com/css2?family=Open+Sans:wght@300;400;600&display=swap">
<style>
:root{
  --black:#000;
  --green:#17a673;
  --green-dark:#11875c;
  --green-dim:#2f5d4b;
  --grey-btn:#7d7d7d;
  --grey-btn-dark:#6a6a6a;
  --text:#333;
  --footer:#1f1f1f;
  --footer-bottom:#121212;
  --footer-text:#e4e4e4;
  --muted:#9a9a9a;
  --white:#fff;
}
*{margin:0;padding:0;box-sizing:border-box}
html,body{width:1098px;height:1200px;overflow:hidden;background:var(--white)}
body{position:relative;font-family:"Open Sans",Arial,sans-serif;color:var(--text)}
.abs{position:absolute}

/* header */
.site-header{left:0;top:0;width:1098px;height:77px;background:var(--black)}
.brand-mark{left:90px;top:12px;font-weight:300;font-size:40px;line-height:48px;color:var(--green);letter-spacing:1px}
.brand-divider{left:206px;top:14px;width:1px;height:49px;background:#ddd}
.brand-tagline{left:213px;top:20px;font-weight:300;font-size:14.5px;line-height:17px;color:#e6e6e6}
.main-nav a{position:absolute;top:31px;font-size:11.5px;color:#d8d8d8;text-decoration:none;line-height:16px}
.main-nav .is-active{left:605px;top:28px;width:62px;height:24px;border:1px solid var(--green);color:var(--green);font-weight:600;text-align:center;line-height:22px}
.nav-divider{left:983px;top:27px;width:1px;height:24px;background:#555}
.nav-search{left:993px;top:32px}

/* hero */
.hero{left:0;top:77px;width:1098px;height:510px;
  background:linear-gradient(180deg,#5f7588 0%,#8499aa 35%,#3e5566 62%,#1c2a33 85%,#2b2a24 100%)}
.hero-arrow{top:302px;width:39px;height:39px;background:rgba(30,30,30,.75)}
.hero-arrow.prev{left:0}
.hero-arrow.next{left:1059px}
.hero-caption{left:209px;top:496px;width:702px;height:59px;background:rgba(20,25,30,.6)}
.hero-caption h2{position:absolute;left:15px;top:15px;font-weight:400;font-size:18.5px;color:var(--white);white-space:nowrap}
.btn-green{background:linear-gradient(180deg,var(--green),var(--green-dark));color:var(--white);text-align:center}
.hero-cta{left:720px;top:511px;width:179px;height:30px;font-size:14.5px;line-height:30px}

/* welcome */
.welcome-title{left:0;top:604px;width:1098px;text-align:center;font-size:24px;font-weight:400;color:#222}
.welcome-sub{left:0;top:636px;width:1098px;text-align:center;font-size:16px;color:#222}
.welcome-text{left:125px;top:664px;width:848px;text-align:center;font-size:11.3px;line-height:15.4px;color:#444}
.read-more{left:487px;top:746px;width:117px;height:31px;font-size:14px;line-height:31px}

/* feature tiles */
.tile{top:837px;width:218px;height:56px;display:flex;align-items:center;justify-content:center;text-align:center;font-size:14.5px;line-height:18px;color:var(--white);border-radius:2px}
.tile.green{background:linear-gradient(180deg,var(--green),var(--green-dark))}
.tile.grey{background:linear-gradient(180deg,#8a8a8a,var(--grey-btn-dark))}

/* footer */
.site-footer{left:0;top:959px;width:1098px;height:196px;background:var(--footer)}
.footer-heading{font-size:14.5px;font-weight:400;color:var(--footer-text)}
.footer-link{font-size:11px;color:var(--footer-text);line-height:14px}
.footer-link .chev{display:inline-block;width:21px;font-size:10px}
.social-dot{width:7px;height:7px;border-radius:50%;background:var(--footer-text)}
.footer-mark{left:749px;top:974px;font-weight:300;font-size:58px;line-height:64px;color:var(--green-dim);letter-spacing:1px}
.search-input{left:756px;top:1077px;width:217px;height:29px;background:#141414}
.search-btn{left:973px;top:1077px;width:34px;height:29px;background:var(--green)}
.footer-small{font-size:9.5px;color:var(--muted)}
.footer-bottom{left:0;top:1155px;width:1098px;height:45px;background:var(--footer-bottom)}
.footer-bottom p{position:absolute;left:0;top:16px;width:1098px;text-align:center;font-size:10px;color:var(--muted)}
</style>
</head>
<body>

<header class="site-header abs">
  <div class="brand-mark abs">krlm</div>
  <div class="brand-divider abs"></div>
  <div class="brand-tagline abs">Keralm Property<br>Development Appraisals</div>
  <nav class="main-nav">
    <a class="is-active" href="#">Home</a>
    <a href="#" style="left:681px">About Us</a>
    <a href="#" style="left:757px">Services</a>
    <a href="#" style="left:830px">Properties</a>
    <a href="#" style="left:913px">Contact Us</a>
  </nav>
  <div class="nav-divider abs"></div>
  <svg class="nav-search abs" width="13" height="13" viewBox="0 0 13 13"><circle cx="5.5" cy="5.5" r="4.3" fill="none" stroke="#bbb" stroke-width="1.3"/><line x1="8.6" y1="8.6" x2="12" y2="12" stroke="#bbb" stroke-width="1.4"/></svg>
</header>

<section class="hero abs" role="img" aria-label="Dusk view of modern glass office towers in a city centre"></section>
<div class="hero-arrow prev abs"><svg width="39" height="39" viewBox="0 0 39 39"><polyline points="22,13 16,19.5 22,26" fill="none" stroke="#fff" stroke-width="2"/></svg></div>
<div class="hero-arrow next abs"><svg width="39" height="39" viewBox="0 0 39 39"><polyline points="17,13 23,19.5 17,26" fill="none" stroke="#fff" stroke-width="2"/></svg></div>
<div class="hero-caption abs"><h2>We are property development and appraisal service</h2></div>
<a class="hero-cta btn-green abs">Call To Action</a>

<h1 class="welcome-title abs">Welcome</h1>
<p class="welcome-sub abs">what problems we can solve</p>
<p class="welcome-text abs">Nunc egestas felis vitae congue tincidunt. Pellentesque ipsum dolor, volutpat id tortor at, dignissim efficitur mauris. Aliquam erat volutpat. Etiam ipsum nibh, porttitor quis molestie id, volutpat in nisi. Morbi vestibulum augue urna, quis fermentum odio pellentesque ac. Donec lacinia lobortis elit id aliquet. Sed tempus et est sit amet scelerisque. Vestibulum rhoncus ligula aliquam elit vehicula, ut venenatis nisi lacinia. Phasellus sit amet aliquam arcu, sit amet ultricies metus. Cum sociis natoque penatibus et magnis dis parturient montes, nascetur ridiculus mus. In sapien velit, vulputate.</p>
<a class="read-more btn-green abs">Read More</a>

<a class="tile green abs" style="left:90px">Email Collection Page</a>
<a class="tile grey abs" style="left:318px">Property Report<br>Page A</a>
<a class="tile grey abs" style="left:547px">Property Report<br>Page B</a>
<a class="tile grey abs" style="left:774px">Property Report<br>Page C</a>

<footer class="site-footer abs"></footer>
<h3 class="footer-heading abs" style="left:92px;top:989px">About Us</h3>
<p class="footer-link abs" style="left:92px;top:1026px"><span class="chev">&gt;&gt;</span>WHO are we?</p>
<p class="footer-link abs" style="left:92px;top:1045px"><span class="chev">&gt;&gt;</span>WHAT do we do?</p>
<p class="footer-link abs" style="left:92px;top:1064px"><span class="chev">&gt;&gt;</span>HOW do we do it?</p>

<h3 class="footer-heading abs" style="left:304px;top:989px">Social Media</h3>
<div class="social-dot abs" style="left:308px;top:1032px"></div><p class="footer-link abs" style="left:338px;top:1028px">Friendwall</p>
<div class="social-dot abs" style="left:308px;top:1054px"></div><p class="footer-link abs" style="left:338px;top:1050px">Chirpline</p>
<div class="social-dot abs" style="left:308px;top:1078px"></div><p class="footer-link abs" style="left:338px;top:1074px">Pinboardly</p>
<div class="social-dot abs" style="left:308px;top:1099px"></div><p class="footer-link abs" style="left:338px;top:1095px">Circleplus</p>

<h3 class="footer-heading abs" style="left:462px;top:989px">Contact Us</h3>
<svg class="abs" style="left:462px;top:1039px" width="12" height="9" viewBox="0 0 12 9"><rect width="12" height="9" rx="1" fill="#e4e4e4"/><polyline points="0.5,0.8 6,5 11.5,0.8" fill="none" stroke="#1f1f1f" stroke-width="1.2"/></svg>
<p class="footer-link abs" style="left:479px;top:1036px;font-size:10px">Email</p>
<p class="footer-link abs" style="left:462px;top:1057px">contactus@keralmappraisals.example</p>

<div class="footer-mark abs">krlm</div>
<h3 class="footer-heading abs" style="left:754px;top:1043px;font-size:13px">Search</h3>
<div class="search-input abs"></div>
<div class="search-btn abs"><svg width="34" height="29" viewBox="0 0 34 29"><circle cx="16" cy="13.5" r="5" fill="none" stroke="#fff" stroke-width="1.6"/><line x1="19.6" y1="17.1" x2="23" y2="20.5" stroke="#fff" stroke-width="1.8"/></svg></div>
<p class="footer-small abs" style="left:757px;top:1114px">FAQ &nbsp;&nbsp;&nbsp;|&nbsp;&nbsp;&nbsp; Sitemap</p>

<div class="footer-bottom abs"><p>©2015 Fennick - Terms of Service - Privacy - Program Policies</p></div>

</body>
</html>
```